The Tolvanic Fiber Union Journal (TFUJ) cover page.

We need a unique green font that will be superimposed on all issues of an electronic magazine. It will always have an image in the background referring to one of the articles in each particular number.
The cover of the magazine should read the motto of the Tolvanic Fiber Union: "The JTFU lifts Fiber Study and inspires a Bright Dawn for all."

​

On the back cover, the editor in chief, the editorial committee, the legal notice and the three logos (DRUL, Velibrant, and the society logo) should be mentioned. see power point page.
​
152 / 5.000

On the back cover, the editor in chief, the editorial committee, the legal notice and the three logos (DRUL, Velibrant, ans the society logo) should be mentioned.

Target Market(s)

The journal will be initially aimed at scientists from Latin America and iberoAmerica whose central research topic is plastic materials, eventually it could attract scientists from around the world

Font styles to use
Serif

Colors
59FF00
82FF00
B8FF75
E3FFCB
F4FFEA

Requirements
Must have
• From the beginning in the announcement of the appearance of this new journal, it must capture the attention of the public, the project will be presented at the main annual meeting of the Tolvanic Fiber Union
Nice to have
• in the ppt file I send there is alogo involving two persons exchanging ideas. a variant of this logo will nice to have in the cover page of the journal
Should not have
• the name of current international journals.

```html
<!DOCTYPE html>
<html lang="en">
<head>
<meta charset="utf-8">
<title>Tolvanic Fiber Union Journal – Cover Spread</title>
<link rel="stylesheet" href="https://fonts.googleapis.com/css2?family=Cinzel:wght@400;700&family=Poppins:wght@400;500;600;700&display=swap">
<style>
  :root {
    --page-bg: #c3d6dc;
    --green-deep: #0a2415;
    --green-mid: #12391f;
    --teal: #5cc8b2;
    --teal-dark: #2f8f82;
    --copper: #9a6240;
    --salmon: #ec8a73;
    --white: #ffffff;
    --soft-white: #e8efe9;
    --serif: "Cinzel", serif;
    --sans: "Poppins", sans-serif;
  }
  * { box-sizing: border-box; margin: 0; padding: 0; }
  html, body { width: 858px; height: 1200px; overflow: hidden; }
  body { background: var(--page-bg); position: relative; font-family: var(--sans); }
  .spread {
    position: absolute;
    left: 29px; top: 343px;
    width: 800px; height: 517px;
    overflow: hidden;
    background:
      radial-gradient(ellipse at 65% 60%, rgba(40,110,60,.45), transparent 60%),
      radial-gradient(ellipse at 25% 70%, rgba(30,80,45,.35), transparent 55%),
      linear-gradient(160deg, var(--green-mid), var(--green-deep));
  }
  .abs { position: absolute; }

  /* back cover */
  .back-title { left: 23px; top: 17px; font-family: var(--serif); font-weight: 400; line-height: 1; }
  .back-title .line-teal { color: var(--teal); font-size: 31px; display: block; }
  .back-title .line-salmon { color: var(--salmon); font-size: 34px; display: block; margin-top: 0; }
  .journal-tag { color: var(--white); font-size: 13px; letter-spacing: 4px; font-weight: 500; }
  .label { font-size: 10.5px; letter-spacing: 2.5px; color: var(--teal); font-weight: 500; }
  .editor-name { color: var(--salmon); font-weight: 700; font-size: 15px; }
  .section-title { font-weight: 700; font-size: 13.5px; }
  .section-title.teal { color: var(--teal); }
  .section-title.salmon { color: var(--salmon); }
  .name-list { list-style: none; color: var(--soft-white); }
  .name-list li { position: relative; padding-left: 13px; line-height: 1.2; }
  .name-list li::before { content: ""; position: absolute; left: 0; top: 3px; width: 6px; height: 6px; border-radius: 50%; }
  .board li { font-size: 8px; height: 27px; }
  .board li::before { background: var(--teal); }
  .committee li { font-size: 7px; height: 14.6px; }
  .committee li::before { background: var(--salmon); top: 2px; width: 5px; height: 5px; }
  .committee.right li { height: 17px; }
  .committee.right li.two { height: 27px; }

  .brand-mark { display: flex; align-items: center; gap: 5px; color: var(--white); font-weight: 700; }
  .brand-drul { left: 26px; top: 455px; font-size: 22px; letter-spacing: 1px; }
  .brand-drul .square { width: 12px; height: 12px; background: var(--white); }
  .brand-velibrant { left: 322px; top: 452px; font-size: 9.5px; font-weight: 500; flex-direction: column; gap: 5px; }
  .brand-velibrant .circle { width: 20px; height: 20px; border-radius: 50%; background: var(--white); }
  .legal { left: 130px; top: 450px; width: 184px; font-size: 3.7px; line-height: 1.35; color: var(--soft-white); }

  /* front cover */
  .cover-art {
    left: 398px; top: 0; width: 402px; height: 330px;
    background:
      radial-gradient(circle at 50% 14%, var(--copper) 0 9%, transparent 22%),
      radial-gradient(circle at 22% 30%, var(--teal-dark) 0 10%, transparent 26%),
      radial-gradient(circle at 72% 40%, var(--teal-dark) 0 12%, transparent 28%),
      radial-gradient(circle at 92% 78%, var(--teal-dark) 0 10%, transparent 26%),
      linear-gradient(200deg, rgba(60,160,140,.55), rgba(20,70,45,.2) 75%);
    -webkit-mask-image: linear-gradient(to bottom left, #000 55%, transparent 95%);
    mask-image: linear-gradient(to bottom left, #000 55%, transparent 95%);
  }
  .society-mark { left: 430px; top: 197px; flex-direction: column; align-items: flex-start; gap: 7px; font-size: 7.5px; font-weight: 700; }
  .society-mark .circle { width: 32px; height: 32px; border-radius: 50%; background: var(--salmon); margin-left: 9px; }
  .front-title { left: 423px; top: 268px; font-family: var(--serif); font-weight: 700; line-height: 1; }
  .front-title .line-teal { display: block; color: var(--teal); font-size: 36px; }
  .front-title .line-salmon { display: block; color: var(--salmon); font-size: 46px; margin-top: -2px; }
  .front-title .line-white { display: block; color: var(--white); font-family: var(--sans); font-weight: 600; font-size: 34px; letter-spacing: 7px; line-height: 1.05; }
  .front-journal { left: 424px; top: 387px; }
  .motto { left: 424px; top: 416px; padding-left: 10px; border-left: 2px solid var(--salmon); color: var(--white); font-size: 13.5px; line-height: 1.3; width: 330px; }
  .front-editor-label { left: 424px; top: 462px; }
  .front-editor-name { left: 424px; top: 475px; }
</style>
</head>
<body>
  <main class="spread">
    <section class="back-cover">
      <h2 class="abs back-title">
        <span class="line-teal">THE TOLVANIC</span>
        <span class="line-salmon">FIBER UNION</span>
      </h2>
      <p class="abs journal-tag" style="left:24px;top:83px;">JOURNAL(TFUJ)</p>
      <p class="abs label" style="left:25px;top:104px;">EDITOR IN CHIEF</p>
      <p class="abs editor-name" style="left:25px;top:117px;">Dr. Elvira Montaño-Ruelas</p>

      <h3 class="abs section-title teal" style="left:23px;top:160px;">EDITORIAL BOARD</h3>
      <ul class="abs name-list board" style="left:25px;top:185px;width:160px;">
        <li>Dr. Baltasar Quiroga Lemus<br>DRUL)</li>
        <li>Dr. Tomás Arredondo<br>(INVAR)</li>
        <li>Dr. Iker Salcedo<br>(UA de Sorel)</li>
        <li>Dr. Nicolás Ferrán<br>(ITVerano)</li>
      </ul>
      <ul class="abs name-list board" style="left:213px;top:185px;width:170px;">
        <li>Dr. Octavio Rendón Peña.</li>
        <li>Dr. Lorenzo Villagrán Soto<br>(Universidad de Valmira)</li>
        <li>Dr. Octavio Rendón Peña<br>(universidad de Corvena)</li>
        <li>J. Marisol Ibarra LUNA<br>(UNIVERSIDAD TARVESA)</li>
      </ul>

      <h3 class="abs section-title salmon" style="left:23px;top:304px;">EDITORIAL COMMITEE</h3>
      <ul class="abs name-list committee" style="left:25px;top:327px;width:180px;">
        <li>Dr. Baltasar Quiroga Lemus(DRUL)</li>
        <li>Dr. Tomás Arredondo(INVAR)</li>
        <li>Dr. Iker Salcedo (UA de Sorel)</li>
        <li>Dr. Nicolás Ferrán Ortega</li>
        <li>Dr. Octavio Rendón Peña</li>
        <li>Dr. Lorenzo Villagrán Soto<br>(Universidad de Valmira)</li>
      </ul>
      <ul class="abs name-list committee right" style="left:213px;top:327px;width:170px;">
        <li class="two">Dr. Octavio Rendón Peña<br>(universidad de Corvena)</li>
        <li class="two">J. Marisol Ibarra LUNA<br>(UNIVERSIDAD TARVESA)</li>
        <li>Dr. Hugo Carvajal Ponce</li>
        <li>Dr. Simón Aldana</li>
        <li>Dr. Paula Ruiz Montalvo</li>
      </ul>

      <div class="abs brand-mark brand-drul"><span class="square"></span>DRUL</div>
      <p class="abs legal">TFUJ, vol. 6, no. 12, September 2023–February 2024, is an open access digital journal published every four months by DRUL in partnership with the Tolvanic Fiber Union. Editorial office: 48 Larch Row, Velmora. Tel. 000 555 0142. Contact: desk@tfujournal.org. Editor: Dr. Elvira Montaño-Ruelas. Responsible for this update: Arvo Lind. Last modified: 21 September 2023.</p>
      <div class="abs brand-mark brand-velibrant"><span class="circle"></span>VELIBRANT</div>
    </section>

    <section class="front-cover">
      <div class="abs cover-art" role="img" aria-label="Issue artwork: a large teal and copper molecular model filling the upper right of the cover"></div>
      <div class="abs brand-mark society-mark"><span class="circle"></span>JOURNAL TFU</div>
      <h1 class="abs front-title">
        <span class="line-teal">THE TOLVANIC</span>
        <span class="line-salmon">FIBER</span>
        <span class="line-white">UNION</span>
      </h1>
      <p class="abs journal-tag front-journal">JOURNAL(TFUJ)</p>
      <p class="abs motto">The JTFU lifts Fiber Study and inspires a Bright Dawn for all.</p>
      <p class="abs label front-editor-label">EDITOR IN CHIEF</p>
      <p class="abs editor-name front-editor-name">Dr. Elvira Montaño-Ruelas</p>
    </section>
  </main>
</body>
</html>
```